DL Cards to get buyers attention

I’m looking to have four double-sided DL flyers professionally prepared and made print-ready in high resolution.

I have uploaded the four existing designs, and I’m happy for them to be reviewed with a fresh set of eyes. While I’m generally happy with the direction, I’m very open to recommendations around layout, typography, imagery, colour balance, spacing and overall presentation if there are opportunities to create a stronger and more professional result.

The key objective is to develop a consistent and recognisable suite of marketing material that strengthens both Lon Pakard brand awareness and my personal profile in the local real estate market. Each flyer should feel like part of the same campaign while still having its own clear message and purpose.

I want the finished designs to feel professional, confident, modern and premium, without becoming overly busy or losing the simplicity that makes a DL flyer easy to read. Strong headlines, clear messaging and an obvious call to action are important. The Lon Pakard branding should be immediately recognisable, while my photograph, name and contact details should be incorporated naturally and consistently.

Please review the existing designs and suggest any changes that would improve their visual impact, readability and consistency. I’m also open to seeing an alternative design direction if you believe there is a better overall look.

The final artwork needs to be supplied professionally print-ready at DL size (210 mm × 99 mm), double-sided, high resolution, CMYK where appropriate, with 3 mm bleed and safe margins, so it can be provided directly to a commercial printer.

The overall goal is simple: strong branding, professional presentation, consistent recognition and marketing material that people will remember.

Target Market(s)

People looking at selling their homes

Industry/Entity Type

Real Estate

Font styles to use
Serif
Sans Serif

Requirements
Must have
• Strong brand awareness - Lon Pakard
Nice to have
• bright and fresh

```html
<!DOCTYPE html>
<html lang="en">
<head>
<meta charset="utf-8">
<title>Lon Pakard – DL Flyer Suite</title>
<link rel="stylesheet" href="https://fonts.googleapis.com/css2?family=Bebas+Neue&family=Montserrat:wght@400;600;700&family=Kaushan+Script&display=swap">
<style>
  :root {
    --bg: #1e1c12;
    --white: #ffffff;
    --ink: #111111;
    --brand-yellow: #f2e21a;
    --bar-grey: #58585a;
    --stripe-grey: #5a5a5a;
  }
  * { margin: 0; padding: 0; box-sizing: border-box; }
  html, body { width: 805px; height: 1200px; overflow: hidden; background: var(--bg); }
  .sheet { position: relative; width: 805px; height: 1200px; }

  .flyer {
    position: absolute; left: 123px; width: 559px; height: 263px;
    background: var(--white); overflow: hidden;
  }
  .flyer--prep { top: 28px; }
  .flyer--ten { top: 322px; }
  .flyer--steps { top: 616px; }
  .flyer--smart { top: 909px; }

  .hero {
    position: absolute; inset: 0;
    clip-path: polygon(359px 0, 559px 0, 559px 263px, 359px 263px, 273px 137px);
  }
  .flyer--prep .hero { background: linear-gradient(170deg, #8fc3e6 0%, #3aa6cf 30%, #2c9bb0 48%, #b9b7ae 70%, #e9ebec 100%); }
  .flyer--ten .hero { background: linear-gradient(180deg, #4a74b8 0%, #6a8fc7 38%, #c9c0b0 55%, #b9ad98 100%); }
  .flyer--steps .hero { background: linear-gradient(175deg, #5f84c6 0%, #8fb0dc 38%, #27b3c1 48%, #d8e2e4 70%, #b8c6c4 100%); }
  .flyer--smart .hero { background: linear-gradient(165deg, #4f6a3a 0%, #2b7a72 35%, #2f8c86 65%, #1f6f6a 100%); }

  .stripe { position: absolute; inset: 0; }
  .stripe--grey { background: var(--stripe-grey); clip-path: polygon(333px 0, 347px 0, 263px 125px); }
  .stripe--yellow { background: var(--brand-yellow); clip-path: polygon(267px 139px, 347px 263px, 314px 263px); }

  .brand {
    position: absolute; right: 22px; top: 16px; text-align: right;
    font-family: "Montserrat", sans-serif; color: var(--white);
  }
  .brand-name {
    display: inline-flex; align-items: center; gap: 6px;
    font-weight: 700; font-size: 13px; line-height: 16px; white-space: nowrap;
  }
  .brand-dot { width: 9px; height: 9px; border-radius: 50%; background: var(--brand-yellow); }
  .brand-office { margin-top: 2px; font-size: 7px; letter-spacing: 0.6px; font-weight: 600; }
  .flyer--prep .brand, .flyer--steps .brand { color: var(--ink); }

  .headline {
    position: absolute; left: 19px;
    font-family: "Bebas Neue", sans-serif; color: var(--ink); white-space: nowrap;
  }
  .headline .accent { color: var(--brand-yellow); }
  .flyer--prep .headline { top: 16px; font-size: 44px; line-height: 36px; }
  .flyer--ten .headline { top: 15px; font-size: 44px; line-height: 37px; letter-spacing: -0.3px; }
  .flyer--steps .headline { top: 16px; font-size: 62px; line-height: 54px; }
  .flyer--smart .headline { top: 19px; left: 22px; font-size: 33px; line-height: 30px; }

  .body-copy {
    position: absolute; left: 22px;
    font-family: "Montserrat", sans-serif; font-size: 12.6px; line-height: 15px; color: var(--ink);
  }
  .body-copy strong { font-weight: 700; }
  .flyer--prep .body-copy { top: 126px; }
  .flyer--ten .body-copy, .flyer--steps .body-copy { top: 134px; }
  .flyer--smart .body-copy { top: 119px; }

  .tagline {
    position: absolute; left: 24px; top: 180px;
    font-family: "Kaushan Script", cursive; font-size: 13px; color: var(--ink); white-space: nowrap;
  }
  .flyer--ten .tagline, .flyer--steps .tagline, .flyer--smart .tagline { top: 183px; }

  .cta-bar {
    position: absolute; left: 0; top: 215px; width: 300px; height: 48px;
    background: var(--bar-grey);
    clip-path: polygon(0 0, 277px 0, 299px 48px, 0 48px);
  }
  .cta-icon { position: absolute; left: 24px; top: 12px; width: 21px; height: 21px; }
  .cta-call {
    position: absolute; left: 51px; top: 7px;
    font-family: "Kaushan Script", cursive; font-size: 20px; color: var(--white); white-space: nowrap;
  }
  .cta-swoosh { position: absolute; left: 60px; top: 29px; width: 70px; height: 8px; }
  .cta-divider { position: absolute; left: 141px; top: 8px; width: 1.5px; height: 29px; background: var(--brand-yellow); }
  .cta-number {
    position: absolute; left: 155px; top: 11px;
    font-family: "Bebas Neue", sans-serif; font-size: 25px; line-height: 25px; color: var(--white); white-space: nowrap;
  }
</style>
</head>
<body>
<main class="sheet">

  <section class="flyer flyer--prep">
    <div class="hero" role="img" aria-label="Aerial view of a harbour and curved beach with the agent in a white shirt smiling"></div>
    <div class="stripe stripe--grey"></div>
    <div class="stripe stripe--yellow"></div>
    <div class="brand"><p class="brand-name"><span class="brand-dot"></span>Lon Pakard</p><p class="brand-office">CORAL POINT</p></div>
    <h2 class="headline">IS YOUR<br>PROPERTY<br><span class="accent">READY TO SELL?</span></h2>
    <p class="body-copy">Local knowledge.<br><strong>Exceptional service.</strong><br>Proven results.</p>
    <p class="tagline">Your property. Our priority.</p>
    <div class="cta-bar">
      <svg class="cta-icon" viewBox="0 0 24 24"><circle cx="12" cy="12" r="12" fill="#fff"/><path d="M8.2 5.8c.5-.3 1.1-.2 1.4.3l1.3 2.2c.3.5.2 1.1-.2 1.4l-.9.7c.6 1.5 1.8 2.8 3.3 3.5l.7-.9c.4-.4 1-.5 1.4-.2l2.2 1.3c.5.3.6.9.3 1.4l-.8 1.2c-.5.7-1.4 1-2.2.8-4-1.2-7-4.3-8.1-8.3-.2-.8.1-1.600.8-2.1z" fill="#58585a"/></svg>
      <span class="cta-call">Call Dane</span>
      <svg class="cta-swoosh" viewBox="0 0 70 8"><path d="M1 7 Q35 -1 69 2" stroke="#f2e21a" stroke-width="2" fill="none" stroke-linecap="round"/></svg>
      <span class="cta-divider"></span>
      <span class="cta-number">0400 123 456</span>
    </div>
  </section>

  <section class="flyer flyer--ten">
    <div class="hero" role="img" aria-label="Beach houses behind sand dunes under blue sky with the agent in a white shirt smiling"></div>
    <div class="stripe stripe--grey"></div>
    <div class="stripe stripe--yellow"></div>
    <div class="brand"><p class="brand-name"><span class="brand-dot"></span>Lon Pakard</p><p class="brand-office">CORAL POINT</p></div>
    <h2 class="headline">10 THINGS TO GET<br>YOUR PROPERTY<br><span class="accent">READY TO SELL?</span></h2>
    <p class="body-copy">A well-prepared home makes<br>a lasting first impression and<br>helps achieve the best result.</p>
    <p class="tagline">Your property. Our priority.</p>
    <div class="cta-bar">
      <svg class="cta-icon" viewBox="0 0 24 24"><circle cx="12" cy="12" r="12" fill="#fff"/><path d="M8.2 5.8c.5-.3 1.1-.2 1.4.3l1.3 2.2c.3.5.2 1.1-.2 1.4l-.9.7c.6 1.5 1.8 2.8 3.3 3.5l.7-.9c.4-.4 1-.5 1.4-.2l2.2 1.3c.5.3.6.9.3 1.4l-.8 1.2c-.5.7-1.4 1-2.2.8-4-1.2-7-4.3-8.1-8.3-.2-.8.1-1.6.8-2.1z" fill="#58585a"/></svg>
      <span class="cta-call">Call Dane</span>
      <svg class="cta-swoosh" viewBox="0 0 70 8"><path d="M1 7 Q35 -1 69 2" stroke="#f2e21a" stroke-width="2" fill="none" stroke-linecap="round"/></svg>
      <span class="cta-divider"></span>
      <span class="cta-number">0400 123 456</span>
    </div>
  </section>

  <section class="flyer flyer--steps">
    <div class="hero" role="img" aria-label="High-rise beachfront tower beside turquoise sea and white sand with the agent in a white shirt smiling"></div>
    <div class="stripe stripe--grey"></div>
    <div class="stripe stripe--yellow"></div>
    <div class="brand"><p class="brand-name"><span class="brand-dot"></span>Lon Pakard</p><p class="brand-office">CORAL POINT</p></div>
    <h2 class="headline">STEPS OF<br><span class="accent">A SALE</span></h2>
    <p class="body-copy">A clear process. Proven results.<br>from listing to settlement, I’m with<br>you every step of the way</p>
    <p class="tagline">Your property. Our priority.</p>
    <div class="cta-bar">
      <svg class="cta-icon" viewBox="0 0 24 24"><circle cx="12" cy="12" r="12" fill="#fff"/><path d="M8.2 5.8c.5-.3 1.1-.2 1.4.3l1.3 2.2c.3.5.2 1.1-.2 1.4l-.9.7c.6 1.5 1.8 2.8 3.3 3.5l.7-.9c.4-.4 1-.5 1.4-.2l2.2 1.3c.5.3.6.9.3 1.4l-.8 1.2c-.5.7-1.4 1-2.2.8-4-1.2-7-4.3-8.1-8.3-.2-.8.1-1.6.8-2.1z" fill="#58585a"/></svg>
      <span class="cta-call">Call Dane</span>
      <svg class="cta-swoosh" viewBox="0 0 70 8"><path d="M1 7 Q35 -1 69 2" stroke="#f2e21a" stroke-width="2" fill="none" stroke-linecap="round"/></svg>
      <span class="cta-divider"></span>
      <span class="cta-number">0400 123 456</span>
    </div>
  </section>

  <section class="flyer flyer--smart">
    <div class="hero" role="img" aria-label="Aerial view of thatched overwater villas and palms in teal water with the agent in a white shirt smiling"></div>
    <div class="stripe stripe--grey"></div>
    <div class="stripe stripe--yellow"></div>
    <div class="brand"><p class="brand-name"><span class="brand-dot"></span>Lon Pakard</p><p class="brand-office">CORAL POINT</p></div>
    <h2 class="headline">THE SMART WAY TO<br>SELL YOUR PROPERTY<br><span class="accent">START WITH KNOWLEDGE</span></h2>
    <p class="body-copy">Inspect your property before<br>you sell and give buyers<br>confidence from day one.</p>
    <p class="tagline">Your property. Our priority.</p>
    <div class="cta-bar">
      <svg class="cta-icon" viewBox="0 0 24 24"><circle cx="12" cy="12" r="12" fill="#fff"/><path d="M8.2 5.8c.5-.3 1.1-.2 1.4.3l1.3 2.2c.3.5.2 1.1-.2 1.4l-.9.7c.6 1.5 1.8 2.8 3.3 3.5l.7-.9c.4-.4 1-.5 1.4-.2l2.2 1.3c.5.3.6.9.3 1.4l-.8 1.2c-.5.7-1.4 1-2.2.8-4-1.2-7-4.3-8.1-8.3-.2-.8.1-1.6.8-2.1z" fill="#58585a"/></svg>
      <span class="cta-call">Call Dane</span>
      <svg class="cta-swoosh" viewBox="0 0 70 8"><path d="M1 7 Q35 -1 69 2" stroke="#f2e21a" stroke-width="2" fill="none" stroke-linecap="round"/></svg>
      <span class="cta-divider"></span>
      <span class="cta-number">0400 123 456</span>
    </div>
  </section>

</main>
</body>
</html>
```